Need business card with a logo for a hearing aid sales and audiology business. We have two Hearing Instrument Specialists and one Audiologist on staff. Over 25 years in business. Locally owned and operated. Financing available. Most insurances accepted.

Summit Audio Wellness LLC
48730 W Larchmont, Suite 7
Spokane, WA 99281
509-617-2084
www.summitaudiowell.example

Manager
Tobias Kerrell HIS COHC
License #71829046

Target Market(s)

50yr old + people with a hearing loss.

Industry/Entity Type

Business

Contact Information for Business Card

48730 W Larchmont, Suite 7
Spokane, WA 99281
509-617-2084
www.summitaudiowell.example

Manager
Tobias Kerrell HIS COHC
NLVE #71829046

Font styles to use
Serif
Sans Serif

Requirements
Must have
• Business name, Tobias's name and title(s) and contact information, License #, web address

```html
<!DOCTYPE html>
<html lang="en">
<head>
<meta charset="utf-8">
<title>Summit Audio Wellness – Business Card</title>
<link rel="stylesheet" href="https://fonts.googleapis.com/css2?family=Roboto:wght@400;500&display=swap">
<style>
  :root {
    --bg: #e9e7e3;
    --card: #ffffff;
    --blue: #6aa7dc;
    --navy: #2b5ea8;
    --green: #1fa77f;
    --icon: #5d7fa8;
    --text-white: #ffffff;
  }
  * { margin: 0; padding: 0; box-sizing: border-box; }
  html, body { width: 1200px; height: 1021px; overflow: hidden; background: var(--bg); }
  body { font-family: "Roboto", Arial, sans-serif; position: relative; }

  .card {
    position: absolute; left: 100px; top: 224px;
    width: 1000px; height: 572px;
    background: var(--card);
    box-shadow: 0 6px 24px rgba(0,0,0,.12);
    overflow: hidden;
  }
  .card-bands { position: absolute; inset: 0; }

  .brand {
    position: absolute; left: 70px; top: 215px;
    display: flex; align-items: center; gap: 18px;
  }
  .brand-dot { width: 54px; height: 54px; border-radius: 50%; background: var(--blue); flex: none; }
  .brand-name {
    font-size: 30px; font-weight: 500; color: var(--navy);
    line-height: 1.15; width: 300px;
  }

  .person { position: absolute; left: 560px; top: 58px; }
  .person-name { font-size: 34px; font-weight: 400; color: var(--navy); }
  .person-role { font-size: 22px; color: var(--green); margin-top: 6px; }
  .person-license { font-size: 17px; color: var(--green); margin-top: 4px; letter-spacing: .5px; }

  .contacts { position: absolute; left: 560px; top: 232px; list-style: none; }
  .contact {
    display: flex; align-items: center; gap: 12px;
    font-size: 19px; color: var(--navy); height: 34px;
  }
  .contact-web { color: var(--green); font-weight: 500; }
  .contact-icon { width: 20px; height: 20px; flex: none; }

  .address {
    position: absolute; left: 70px; top: 500px;
    color: var(--text-white); font-size: 22px; line-height: 1.3;
  }
</style>
</head>
<body>
  <article class="card">
    <svg class="card-bands" width="1000" height="572" viewBox="0 0 1000 572" aria-hidden="true">
      <polygon class="band-green" points="536,474 610,384 1000,384 1000,404 622,404 556,484" fill="var(--green)"/>
      <polygon class="band-blue" points="0,488 566,488 632,412 1000,412 1000,572 0,572" fill="var(--blue)"/>
    </svg>

    <div class="brand">
      <span class="brand-dot"></span>
      <span class="brand-name">Summit Audio Wellness LLC</span>
    </div>

    <header class="person">
      <h1 class="person-name">Tobias Kerrell HIS COHC</h1>
      <p class="person-role">Manager</p>
      <p class="person-license">NLVE #71829046</p>
    </header>

    <ul class="contacts">
      <li class="contact">
        <svg class="contact-icon" viewBox="0 0 20 20"><circle cx="10" cy="10" r="10" fill="var(--icon)"/><path d="M7 5l2 2-1 1.5c.7 1.5 1.8 2.6 3.3 3.3L12.8 11l2 2-1.5 1.7C9.5 14.3 5.7 10.5 5.3 6.7z" fill="#fff"/></svg>
        509-617-2084
      </li>
      <li class="contact">
        <svg class="contact-icon" viewBox="0 0 20 20"><circle cx="10" cy="10" r="10" fill="var(--icon)"/><rect x="5" y="6.5" width="10" height="7" fill="#fff"/><path d="M5 6.5l5 4 5-4" stroke="var(--icon)" fill="none" stroke-width="1.2"/></svg>
        hello@summitaudiowell.example
      </li>
      <li class="contact contact-web">
        <svg class="contact-icon" viewBox="0 0 20 20"><circle cx="10" cy="10" r="10" fill="var(--icon)"/><circle cx="10" cy="10" r="5.5" fill="none" stroke="#fff" stroke-width="1.2"/><path d="M4.5 10h11M10 4.5c-2.5 3-2.5 8 0 11M10 4.5c2.5 3 2.5 8 0 11" stroke="#fff" fill="none" stroke-width="1"/></svg>
        www.summitaudiowell.example
      </li>
    </ul>

    <address class="address">
      48730 W Larchmont, Suite 7<br>
      Spokane, WA 99281
    </address>
  </article>
</body>
</html>
```